Folded A4 flyer for design&construction company

Folded A4 flyer needed. Keywords: elegant, stylish
our website www.dorvika.ae

Industry/Entity Type

Construction

```html
<!DOCTYPE html>
<html lang="en">
<head>
<meta charset="utf-8">
<title>Dorvika — Folded Flyer</title>
<link rel="stylesheet" href="https://fonts.googleapis.com/css2?family=Roboto:wght@400;500&family=Bebas+Neue&display=swap">
<style>
  :root {
    --gold: #a07a2c;
    --gold-deep: #8c6a24;
    --ink: #222222;
    --text: #333333;
    --footer: #1e1e1e;
    --paper: #ffffff;
    --backdrop: #ececec;
    --photo-warm: #d9a43a;
    --photo-light: #efe7d9;
  }
  * { margin: 0; padding: 0; box-sizing: border-box; }
  html, body { width: 1200px; height: 847px; overflow: hidden; }
  body { background: var(--backdrop); font-family: "Roboto", Arial, sans-serif; color: var(--text); position: relative; }

  .spread { position: absolute; left: 121px; top: 82px; width: 1049px; height: 690px; background: var(--paper); overflow: hidden; }
  .page { position: absolute; top: 0; height: 690px; }
  .page--cover { left: 0; width: 484px; }
  .page--inside { left: 484px; width: 565px; }

  .band-top { position: absolute; left: 0; top: 0; width: 100%; height: 34px; background: var(--gold); }
  .band-footer { position: absolute; left: 0; bottom: 0; width: 100%; height: 50px; background: var(--footer); color: #fff; font-size: 12px; line-height: 15px; text-align: center; padding-top: 4px; }

  .cover-photo { position: absolute; left: 0; top: 34px; width: 484px; height: 430px;
    background: linear-gradient(180deg, #e6e6e6 0%, #f1f1f1 45%, #fbfbfb 80%, #ffffff 100%); }

  .brand-name { font-family: "Roboto", Arial, sans-serif; font-weight: 400; color: var(--ink); letter-spacing: 1px; text-align: center; position: absolute; }
  .cover-brand { left: 0; width: 484px; top: 380px; font-size: 38px; }
  .cover-quote { position: absolute; left: 0; width: 484px; top: 447px; text-align: center; font-size: 20px; color: var(--ink); }

  .badge { position: absolute; left: 0; top: 0; }
  .inside-brand { left: 115px; width: 250px; top: 72px; font-size: 44px; }

  .inside-photo { position: absolute; left: 2px; top: 174px; width: 515px; height: 310px;
    background: linear-gradient(120deg, #e9e4dc 0%, var(--photo-light) 30%, var(--photo-warm) 60%, #c98a2a 80%, #eeeae4 100%); }

  .about { position: absolute; left: 14px; top: 514px; width: 266px; font-size: 10.2px; line-height: 12.1px; text-align: justify; color: var(--ink); }

  .quote-cta { position: absolute; left: 268px; width: 228px; top: 524px; text-align: center; }
  .quote-cta h2 { font-family: "Bebas Neue", "Oswald", sans-serif; font-weight: 400; font-size: 25px; color: var(--gold-deep); letter-spacing: 0.3px; }
  .contact-line { font-size: 13px; line-height: 15.5px; color: var(--ink); margin-top: 1px; display: flex; justify-content: center; align-items: center; gap: 6px; }
  .contact-line svg { width: 12px; height: 12px; fill: var(--gold); }
  .contact-first { margin-top: 8px; }
</style>
</head>
<body>
  <div class="spread">
    <section class="page page--cover">
      <div class="band-top"></div>
      <div class="cover-photo" role="img" aria-label="Faded bright white living room interior with tall windows"></div>
      <div class="brand-name cover-brand">DORVIKA</div>
      <p class="cover-quote">Quality is not an act, it is a habit – Theron</p>
      <footer class="band-footer">www.dorvika.ae<br>Dorvika LLC, Marlow Tower, Office 1207, Harbor District, Dubai</footer>
    </section>

    <section class="page page--inside">
      <div class="band-top"></div>
      <svg class="badge" width="565" height="160" viewBox="0 0 565 160" aria-hidden="true">
        <circle cx="243" cy="28" r="124" fill="#ffffff" stroke="#a07a2c" stroke-width="2"/>
      </svg>
      <div class="brand-name inside-brand">DORVIKA</div>

      <div class="inside-photo" role="img" aria-label="Modern interior with curved orange ceiling, spiral staircase, wooden floor and lounge chairs"></div>

      <p class="about">We believe in quality beginnings and flawless finishes. We are a team of creative designers and constructors with years of experience and expertise in providing complete interior design and construction services. Our unique designing prowess is complemented by our unflinching commitment to quality construction. Our team specializes in classic and contemporary high quality construction in Dubai for commercial and residential projects.</p>

      <div class="quote-cta">
        <h2>Get a free quote today!</h2>
        <p class="contact-line contact-first">
          <svg viewBox="0 0 24 24"><path d="M6.6 10.8c1.4 2.8 3.8 5.1 6.6 6.6l2.2-2.2c.3-.3.7-.4 1-.2 1.1.4 2.3.6 3.6.6.6 0 1 .4 1 1V20c0 .6-.4 1-1 1C10.6 21 3 13.4 3 4c0-.6.4-1 1-1h3.5c.6 0 1 .4 1 1 0 1.3.2 2.5.6 3.6.1.3 0 .7-.2 1z"/></svg>
          800 – dorvika
        </p>
        <p class="contact-line">or</p>
        <p class="contact-line">
          <svg viewBox="0 0 24 24"><path d="M2 6h20v12H2z M2 6l10 7 10-7" /></svg>
          contact@dorvika.ae
        </p>
      </div>

      <footer class="band-footer">www.dorvika.ae<br>Dorvika LLC, Marlow Tower, Office 1207, Harbor District, Dubai</footer>
    </section>
  </div>
</body>
</html>
```